BRELDON ELECTRICAL

all black background with silver and lime writing, fonts i like are gothic style but am open to ideas, will need a picture logo aswell as im putting this on my van.i am a electrical contractor starting up my own electrical business. underneath breldon electrical heading on card we could put" professiona cost effective soloutions to all your electrical needs".{ or something of that nature }.on aback of card on top half list servises provided, real estate and commercial maintenance, new home and renovation rewires and upgrades, split system air conditioning, floor heat, tv phone data, smoke detoctors, lighting systems , builders welcome, , and also a thankyou for your business.

Contact Information for Business Card

GARETH PILKSWORTH
breldonelectrical@quivmail.com.au
0413927154
lic no 58190
ac lic no l263917
abn 31726458103

```html
<!DOCTYPE html>
<html lang="en">
<head>
<meta charset="utf-8">
<title>Breldon Electrical – Business Card</title>
<link href="https://fonts.googleapis.com/css2?family=Open+Sans:wght@400;600;700&display=swap" rel="stylesheet">
<style>
  :root {
    --backdrop: #2a2723;
    --card: #0b0b0b;
    --card-edge: #1c1c1c;
    --lime: #8fe21a;
    --silver: #d9d9d9;
    --white: #ffffff;
    --muted: #7d7d7d;
  }
  * { margin: 0; padding: 0; box-sizing: border-box; }
  html, body {
    width: 1200px; height: 1023px; overflow: hidden;
    background: var(--backdrop);
    font-family: "Open Sans", Arial, sans-serif;
  }
  .sheet {
    position: relative; width: 1200px; height: 1023px;
    display: flex; flex-direction: column; align-items: center;
    justify-content: center; gap: 39px;
  }
  .card {
    position: relative; width: 740px; height: 452px;
    background: radial-gradient(ellipse at 50% 30%, #1a1a1a 0%, var(--card) 70%);
    border: 1px solid var(--card-edge);
    box-shadow: 0 10px 30px rgba(0,0,0,.5);
    overflow: hidden;
  }

  /* Back of card */
  .services {
    position: absolute; left: 60px; top: 46px; width: 400px; text-align: center;
  }
  .services__title {
    color: var(--lime); font-weight: 700; font-size: 19px; letter-spacing: .3px;
    padding-bottom: 10px; border-bottom: 1px solid var(--lime);
  }
  .services__list {
    list-style: none; margin-top: 12px;
    color: var(--silver); font-size: 17px; line-height: 27px;
  }
  .back-brand {
    position: absolute; right: 46px; top: 196px;
    display: flex; align-items: center; gap: 10px;
    color: var(--lime); font-weight: 700; font-size: 30px; letter-spacing: 1px;
  }
  .back-brand__dot { width: 18px; height: 18px; border-radius: 50%; background: var(--lime); }
  .back-note {
    position: absolute; left: 0; right: 0; bottom: 30px; text-align: center;
    color: var(--silver); font-size: 15px;
  }

  /* Front of card */
  .front { text-align: center; }
  .brand {
    margin-top: 92px;
    display: inline-flex; align-items: center; gap: 14px;
    color: var(--lime); font-weight: 600; font-size: 48px; letter-spacing: 2px;
  }
  .brand__mark { width: 26px; height: 26px; background: var(--lime); }
  .tagline {
    margin-top: 6px; color: var(--lime); font-weight: 600; font-size: 16px;
  }
  .contact { margin-top: 58px; }
  .contact__name { color: var(--lime); font-weight: 600; font-size: 21px; letter-spacing: .5px; }
  .contact__line {
    display: flex; align-items: center; justify-content: center; gap: 8px;
    color: var(--white);
  }
  .contact__phone { font-size: 21px; font-weight: 600; margin-top: 4px; }
  .contact__email { font-size: 17px; margin-top: 2px; }
  .contact__email .hl { color: var(--lime); }
  .licences {
    position: absolute; left: 0; right: 0; bottom: 24px;
    color: var(--muted); font-size: 13px; word-spacing: 2px;
  }
  .licences span { margin: 0 8px; }
</style>
</head>
<body>
<main class="sheet">

  <section class="card back" aria-label="Card back">
    <div class="services">
      <h2 class="services__title">Services Provided:</h2>
      <ul class="services__list">
        <li>Real estate and commercial maintenance</li>
        <li>New home and renovation rewires and upgrades</li>
        <li>Split system air conditioning</li>
        <li>Floor heat</li>
        <li>TV phone data</li>
        <li>Smoke detectors</li>
        <li>Lighting systems</li>
      </ul>
    </div>
    <div class="back-brand"><span class="back-brand__dot"></span>BRELDON</div>
    <p class="back-note">Builders welcome, thank you for your business</p>
  </section>

  <section class="card front" aria-label="Card front">
    <h1 class="brand"><span class="brand__mark"></span>BRELDON ELECTRICAL</h1>
    <p class="tagline">Professional cost effective soloutions to all your electrical needs</p>
    <div class="contact">
      <p class="contact__name">GARETH PILKSWORTH</p>
      <p class="contact__line contact__phone">
        <svg width="12" height="20" viewBox="0 0 12 20" aria-hidden="true">
          <rect x="1" y="1" width="10" height="18" rx="2" fill="none" stroke="#8fe21a" stroke-width="2"/>
          <circle cx="6" cy="15.5" r="1.2" fill="#8fe21a"/>
        </svg>
        041 392 7154
      </p>
      <p class="contact__line contact__email">
        <svg width="16" height="11" viewBox="0 0 16 11" aria-hidden="true">
          <rect width="16" height="11" fill="#8fe21a"/>
          <path d="M0 0 L8 6 L16 0" fill="none" stroke="#0b0b0b" stroke-width="1.4"/>
        </svg>
        <span>breldon<span class="hl">electrical</span>@quivmail.com.au</span>
      </p>
    </div>
    <p class="licences">License No : 58190<span>|</span>AC Licence No : 263917<span>|</span>ABN : 31726458103</p>
  </section>

</main>
</body>
</html>
```